Larkfield Ridge Management

I need a professional website. My current website is larkfieldridgemanagement.com and I hate it. It was created with some AI tool very quickly because I needed a site up and running with no advanced notice. I’m open to all designs .. I trust you, the professionals will deliver the results I’m anxiously awaiting! :)

```html
<!DOCTYPE html>
<html lang="en">
<head>
<meta charset="utf-8">
<title>Larkfield Ridge Management</title>
<link href="https://fonts.googleapis.com/css2?family=Oswald:wght@500;600;700&family=Inter:wght@400;500;600&display=swap" rel="stylesheet">
<style>
:root{
  --navy:#1c2a4d;
  --navy-deep:#16223f;
  --red:#b8192a;
  --red-soft:#c4283a;
  --ink:#222631;
  --muted:#4a4f5c;
  --line:#d9dce3;
  --green:#2fb52a;
  --white:#fff;
}
*{margin:0;padding:0;box-sizing:border-box}
html,body{width:1200px;height:4528px;overflow:hidden}
body{position:relative;background:var(--white);font-family:"Inter",Arial,sans-serif;color:var(--ink)}
.abs{position:absolute}
.display{font-family:"Oswald","Arial Narrow",sans-serif;font-weight:600;color:var(--navy);letter-spacing:.2px}
.btn{position:absolute;background:var(--red);color:#fff;font-size:16px;display:flex;align-items:center;justify-content:center;border-radius:5px}
.eyebrow{position:absolute;display:flex;align-items:center;gap:12px;color:var(--red);font-size:14px}
.eyebrow svg{width:24px;height:24px;fill:var(--navy)}
.brand{font-family:"Oswald","Arial Narrow",sans-serif;font-weight:700;color:var(--navy);text-transform:uppercase;text-align:center;line-height:1.05;display:flex;align-items:center;justify-content:center;gap:8px}
.brand i{display:block;width:12px;height:12px;background:var(--red)}

/* hero */
.hero-photo{position:absolute;left:0;top:0;width:1200px;height:860px;clip-path:polygon(0 0,100% 0,100% 730px,50% 860px,0 730px);
  background:linear-gradient(90deg,rgba(248,250,252,.96) 0%,rgba(240,244,248,.85) 35%,rgba(220,228,236,.2) 70%),linear-gradient(180deg,#b9c8d8 0%,#e5e9ee 55%,#cfd4d6 100%)}
.nav a{position:absolute;top:70px;font-size:16px;color:var(--ink);text-decoration:none}
.nav a.active{color:var(--red)}
.hero-title{position:absolute;left:125px;top:246px;font-size:58px;line-height:61px;text-transform:uppercase;font-weight:700}
.hero-title span{color:var(--red)}
.stat{position:absolute;top:612px;width:220px}
.stat b{display:block;font-family:"Oswald",sans-serif;font-weight:500;font-size:33px;color:var(--navy)}
.stat p{font-size:14px;line-height:21px;color:var(--muted);margin-top:8px}

/* services */
.lead{position:absolute;font-size:13px;line-height:19px;color:var(--muted)}
.card{position:absolute;top:1190px;width:303px;height:507px;text-align:center;border-radius:14px}
.card.featured{border:1.5px solid #d68a93}
.card .photo{width:303px;height:250px;border-radius:14px}
.card h3{font-family:"Oswald",sans-serif;font-weight:500;font-size:22px;color:var(--navy);margin-top:14px}
.card p{font-size:13px;line-height:22px;color:var(--muted);margin:10px 26px 0}
.card .btn{left:84px;top:444px;width:134px;height:44px}

/* about */
.about{position:absolute;left:0;top:1796px;width:1200px;height:700px;background:linear-gradient(180deg,#e4e8ee 0%,#d6dbe2 60%,#cdd2d8 100%)}
.about p{font-size:13.5px;line-height:19.5px;color:var(--muted)}

/* table */
.table{position:absolute;left:125px;top:2795px;width:949px;border-radius:12px;overflow:hidden;box-shadow:0 2px 10px rgba(0,0,0,.08)}
.row{display:grid;grid-template-columns:416px 324px 209px;height:58px;align-items:center;border-top:1px solid var(--line);font-size:15px}
.row>div{height:100%;display:flex;align-items:center;padding-left:36px;border-right:1px solid var(--line)}
.row>div:last-child{border-right:none;padding-left:26px}
.row.head{background:var(--navy);color:#fff;height:66px;border-top:none;font-weight:500;font-size:17px}
.row.head>div{border-color:rgba(255,255,255,.35);padding-left:30px}
.market{font-weight:600;gap:14px}
.market svg{width:18px;height:20px;fill:var(--red)}
.pill{width:150px;height:34px;border-radius:17px;color:#fff;font-size:12px;display:flex;align-items:center;justify-content:center;background:var(--green)}
.pill.wait{background:var(--red)}

/* inquiry */
.inquiry{position:absolute;left:0;top:3263px;width:1200px;height:910px;background:linear-gradient(160deg,#2a3d6b 0%,#22345e 50%,#1b2b50 100%)}
.field{position:absolute;background:#fff;border-radius:5px;font-size:12px;color:#9aa0aa;padding:14px 12px}

/* footer */
.foot-col h4{font-family:"Oswald",sans-serif;font-weight:500;font-size:17px;color:var(--red)}
.foot-col li{list-style:none;font-size:15px;margin-top:10px;display:flex;align-items:center;gap:12px;height:17px}
.foot-col li svg{width:13px;height:13px;fill:var(--red)}
</style>
</head>
<body>

<!-- HERO -->
<div class="hero-photo" role="img" aria-label="Modern white apartment building under a soft blue sky"></div>
<svg class="abs" style="left:0;top:700px" width="1200" height="170" viewBox="0 700 1200 170">
  <polygon points="0,725 600,842 600,862 0,770" fill="var(--red)"/>
  <polygon points="1200,725 600,842 600,862 1200,770" fill="var(--navy)"/>
</svg>

<nav class="nav">
  <a class="active" style="left:125px">Home</a>
  <a style="left:205px">About Us</a>
  <a style="left:311px">Services</a>
  <a style="left:413px">Why Us</a>
  <a style="left:679px">Service Areas</a>
  <a style="left:822px">Contact</a>
</nav>
<div class="brand abs" style="left:500px;top:45px;width:180px;height:70px;font-size:24px"><i></i>Larkfield Ridge</div>
<div class="btn" style="left:907px;top:54px;width:168px;height:50px;font-weight:500">Get A Proposal</div>

<div class="eyebrow" style="left:125px;top:192px;font-size:15px"><svg viewBox="0 0 24 24"><path d="M12 1l3.2 7.2 7.8.8-5.9 5.3 1.7 7.7L12 18l-6.8 4 1.7-7.7L1 9l7.8-.8z"/></svg>Cleveland &amp; Akron, Ohio</div>
<h1 class="hero-title display">Property<br>Management That<br>Treats Your Building<br><span>Like It's Ours.</span></h1>
<div class="btn" style="left:125px;top:505px;width:225px;height:49px">Request A Proposal</div>

<div class="stat" style="left:125px"><b>1,200+</b><p>Units Under Management Across Cuyahoga &amp; Summit County</p></div>
<div class="stat" style="left:366px"><b>11 Yrs</b><p>Average Tenure Of Our Regional Maintenance Leads</p></div>
<div class="stat" style="left:608px"><b>&lt; 4 Hrs</b><p>Average Response Time On Urgent Maintenance Requests</p></div>
<div class="stat" style="left:850px;width:240px"><b>96%</b><p>Owner Retention Rate Over The Past Five Years</p></div>

<!-- SERVICES -->
<div class="eyebrow" style="left:125px;top:979px"><svg viewBox="0 0 24 24"><path d="M12 1l3.2 7.2 7.8.8-5.9 5.3 1.7 7.7L12 18l-6.8 4 1.7-7.7L1 9l7.8-.8z"/></svg>Our Service</div>
<h2 class="display abs" style="left:125px;top:1022px;font-size:44px;line-height:50px">Strategic Property<br>Management Solutions</h2>
<div class="lead" style="left:611px;top:978px;width:465px">Our Analysis Demonstrates That Effective Property Oversight Originates From Meticulous Operational Planning, Transparent Communication Channels, And Data-Driven Performance Metrics Across Every Asset Class.<br><br>By Integrating Advanced Technology With Industry Expertise, Our Team Implements Proactive Maintenance Schedules That Preserve Asset Value And Facilitate Sustainable, Long-Term Returns For Stakeholders.</div>

<div class="card" style="left:126px">
  <div class="photo" role="img" aria-label="Agent signing a contract beside a small model house" style="background:linear-gradient(135deg,#3e4f66,#8a96a6 60%,#d8a35a)"></div>
  <h3>Basic Service</h3>
  <p>Describe Important Details Like Price, Value, Length Of Service, And Why It's Unique. Or Use These Sections To Showcase Different Key Values Of Your Products Or Services.</p>
  <div class="btn">Learn More</div>
</div>
<div class="card featured" style="left:453px">
  <div class="photo" role="img" aria-label="Street of brick townhouses with green lawns" style="background:linear-gradient(180deg,#9ec3e6,#8c6b55 50%,#5f8a45)"></div>
  <h3>Intermediate Service</h3>
  <p>Describe Important Details Like Price, Value, Length Of Service, And Why It's Unique. Or Use These Sections To Showcase Different Key Values Of Your Products Or Services.</p>
  <div class="btn">Learn More</div>
</div>
<div class="card" style="left:771px">
  <div class="photo" role="img" aria-label="Row of suburban homes with garages" style="background:linear-gradient(180deg,#a9c8e8,#6d7f92 55%,#7aa35a)"></div>
  <h3>Advanced Service</h3>
  <p>Describe Important Details Like Price, Value, Length Of Service, And Why It's Unique. Or Use These Sections To Showcase Different Key Values Of Your Products Or Services.</p>
  <div class="btn">Learn More</div>
</div>

<!-- ABOUT -->
<section class="about" role="img" aria-label="Faded aerial view of a residential neighborhood">
  <svg class="abs" style="left:63px;top:84px" width="520" height="541" viewBox="0 0 520 541">
    <polygon points="260,6 514,150 514,392 260,536 6,392 6,150" fill="var(--navy)"/>
    <polygon points="260,30 490,162 490,380 260,512 30,380 30,162" fill="#b9a893" role="img" aria-label="Agent handing house keys to a smiling couple"/>
  </svg>
  <div class="eyebrow" style="left:618px;top:118px"><svg viewBox="0 0 24 24"><path d="M12 1l3.2 7.2 7.8.8-5.9 5.3 1.7 7.7L12 18l-6.8 4 1.7-7.7L1 9l7.8-.8z"/></svg>About Us</div>
  <h2 class="display abs" style="left:618px;top:162px;font-size:44px;line-height:50px">About Our Property<br>Management Solutions</h2>
  <div class="abs" style="left:618px;top:284px;width:466px">
    <p>Our Organization Delivers Comprehensive Property Management Solutions That Optimize Asset Performance And Tenant Satisfaction. By Integrating Advanced Analytics With Proven Operational Frameworks, Our Specialists Ensure Each Property Achieves Sustained Value Appreciation.</p>
    <p style="margin-top:20px">Drawing On Decades Of Collective Expertise, The Team Facilitates Regulatory Compliance, Cost Efficiency, And Proactive Maintenance. This Disciplined Approach Enables Owners To Preserve Capital, Enhance Occupancy Rates, And Demonstrate Long-Term Resilience Across Diverse Market Conditions.</p>
  </div>
  <div class="btn" style="left:618px;top:519px;width:178px;height:45px">Learn More</div>
</section>

<!-- SERVICE AREAS -->
<div class="eyebrow" style="left:125px;top:2615px"><svg viewBox="0 0 24 24"><path d="M12 1l3.2 7.2 7.8.8-5.9 5.3 1.7 7.7L12 18l-6.8 4 1.7-7.7L1 9l7.8-.8z"/></svg>Service Areas</div>
<h2 class="display abs" style="left:125px;top:2660px;font-size:44px;line-height:50px">Managing Property Across<br>Five Northeast Ohio Markets.</h2>
<div class="lead" style="left:687px;top:2671px;width:370px">Don't See Your Area Listed? We're Expanding — Get In Touch.</div>

<div class="table">
  <div class="row head"><div>Market</div><div>Property Type</div><div>Status</div></div>
  <div class="row"><div class="market"><svg viewBox="0 0 18 20"><path d="M9 0a7 7 0 0 0-7 7c0 5 7 13 7 13s7-8 7-13a7 7 0 0 0-7-7zm0 9.5A2.5 2.5 0 1 1 9 4.5a2.5 2.5 0 0 1 0 5z"/></svg>Cleveland &amp; Tremont</div><div>Multifamily, Single-Family</div><div><span class="pill">Accepting Owners</span></div></div>
  <div class="row"><div class="market"><svg viewBox="0 0 18 20"><path d="M9 0a7 7 0 0 0-7 7c0 5 7 13 7 13s7-8 7-13a7 7 0 0 0-7-7zm0 9.5A2.5 2.5 0 1 1 9 4.5a2.5 2.5 0 0 1 0 5z"/></svg>Lakewood</div><div>Multifamily</div><div><span class="pill">Accepting Owners</span></div></div>
  <div class="row"><div class="market"><svg viewBox="0 0 18 20"><path d="M9 0a7 7 0 0 0-7 7c0 5 7 13 7 13s7-8 7-13a7 7 0 0 0-7-7zm0 9.5A2.5 2.5 0 1 1 9 4.5a2.5 2.5 0 0 1 0 5z"/></svg>Akron</div><div>Single-Family, Small Multifamily</div><div><span class="pill">Accepting Owners</span></div></div>
  <div class="row"><div class="market"><svg viewBox="0 0 18 20"><path d="M9 0a7 7 0 0 0-7 7c0 5 7 13 7 13s7-8 7-13a7 7 0 0 0-7-7zm0 9.5A2.5 2.5 0 1 1 9 4.5a2.5 2.5 0 0 1 0 5z"/></svg>Cuyahoga Falls</div><div>Single-Family</div><div><span class="pill">Accepting Owners</span></div></div>
  <div class="row"><div class="market"><svg viewBox="0 0 18 20"><path d="M9 0a7 7 0 0 0-7 7c0 5 7 13 7 13s7-8 7-13a7 7 0 0 0-7-7zm0 9.5A2.5 2.5 0 1 1 9 4.5a2.5 2.5 0 0 1 0 5z"/></svg>Shaker Heights</div><div>Multifamily</div><div><span class="pill wait">Waitlist</span></div></div>
</div>

<!-- INQUIRY -->
<section class="inquiry">
  <svg class="abs" style="left:588px;top:80px" width="24" height="24" viewBox="0 0 24 24"><path fill="#fff" d="M12 1l3.2 7.2 7.8.8-5.9 5.3 1.7 7.7L12 18l-6.8 4 1.7-7.7L1 9l7.8-.8z"/></svg>
  <div class="abs" style="left:0;top:114px;width:1200px;text-align:center;font-size:14px;color:var(--red-soft)">Service Areas</div>
  <h2 class="display abs" style="left:0;top:151px;width:1200px;text-align:center;font-size:44px;color:#fff">Submit Your Property Management Inquiry</h2>
  <div class="field" style="left:125px;top:274px;width:466px;height:46px">First Name</div>
  <div class="field" style="left:608px;top:274px;width:466px;height:46px">Last Name</div>
  <div class="field" style="left:125px;top:346px;width:466px;height:46px">Email</div>
  <div class="field" style="left:608px;top:346px;width:466px;height:46px">Phone</div>
  <div class="field" style="left:125px;top:418px;width:949px;height:163px">Message</div>
  <div class="btn" style="left:511px;top:669px;width:176px;height:43px">Send Now</div>
</section>
<svg class="abs" style="left:0;top:4030px" width="1200" height="145" viewBox="0 4030 1200 145">
  <polygon points="0,4175 600,4062 1200,4175" fill="#fff"/>
  <polygon points="0,4132 600,4040 600,4060 0,4172" fill="var(--navy-deep)"/>
  <polygon points="1200,4132 600,4040 600,4060 1200,4172" fill="var(--red)"/>
</svg>

<!-- FOOTER -->
<div class="brand abs" style="left:122px;top:4260px;width:190px;height:80px;font-size:24px"><i></i>Larkfield Ridge</div>

<div class="foot-col abs" style="left:367px;top:4226px">
  <h4>Company</h4>
  <ul style="margin-top:18px">
    <li><svg viewBox="0 0 24 24"><path d="M12 1l3.2 7.2 7.8.8-5.9 5.3 1.7 7.7L12 18l-6.8 4 1.7-7.7L1 9l7.8-.8z"/></svg>About</li>
    <li><svg viewBox="0 0 24 24"><path d="M12 1l3.2 7.2 7.8.8-5.9 5.3 1.7 7.7L12 18l-6.8 4 1.7-7.7L1 9l7.8-.8z"/></svg>Services</li>
    <li><svg viewBox="0 0 24 24"><path d="M12 1l3.2 7.2 7.8.8-5.9 5.3 1.7 7.7L12 18l-6.8 4 1.7-7.7L1 9l7.8-.8z"/></svg>Service Areas</li>
  </ul>
</div>
<div class="foot-col abs" style="left:529px;top:4226px">
  <h4>Contact</h4>
  <ul style="margin-top:18px">
    <li><svg viewBox="0 0 24 24"><path d="M2 5h20v14H2zM2 5l10 8 10-8" stroke="#fff" stroke-width="1.5"/></svg>Hello@Larkfieldridgemanagement.com</li>
    <li><svg viewBox="0 0 24 24"><path d="M6 2l4 5-2 3a12 12 0 0 0 6 6l3-2 5 4-3 4C10 22 2 14 2 5z"/></svg>(216) 555-0193</li>
    <li><svg viewBox="0 0 18 20"><path d="M9 0a7 7 0 0 0-7 7c0 5 7 13 7 13s7-8 7-13a7 7 0 0 0-7-7zm0 9.5A2.5 2.5 0 1 1 9 4.5a2.5 2.5 0 0 1 0 5z"/></svg>Cleveland, OH</li>
  </ul>
</div>
<div class="foot-col abs" style="left:873px;top:4226px">
  <h4>Follow</h4>
  <ul style="margin-top:18px">
    <li style="gap:8px"><svg viewBox="0 0 24 24"><path d="M12 1l3.2 7.2 7.8.8-5.9 5.3 1.7 7.7L12 18l-6.8 4 1.7-7.7L1 9l7.8-.8z"/></svg>Photo Journal</li>
    <li style="gap:8px"><svg viewBox="0 0 24 24"><path d="M12 1l3.2 7.2 7.8.8-5.9 5.3 1.7 7.7L12 18l-6.8 4 1.7-7.7L1 9l7.8-.8z"/></svg>Career Network</li>
    <li style="gap:8px"><svg viewBox="0 0 24 24"><path d="M12 1l3.2 7.2 7.8.8-5.9 5.3 1.7 7.7L12 18l-6.8 4 1.7-7.7L1 9l7.8-.8z"/></svg>Community Page</li>
  </ul>
</div>
<div class="abs" style="left:125px;top:4436px;width:949px;height:1px;background:var(--line)"></div>
<div class="abs" style="left:0;top:4472px;width:1200px;text-align:center;font-size:15px">© 2026 Larkfield Ridge Management, LLC</div>

</body>
</html>
```